Harrow Grading LLC business card design

Excavation company business cards

Contact Information for Business Card

Harrow Grading LLC cell phone 208-417-6290 office phone 208-319-4856 harrowgradingllc@maplecove.com Driveways, site prep, retaining walls, septic systems, rock delivery

Colors

Designer to choose colors to be used in the design.

```html
<!DOCTYPE html>
<html lang="en">
<head>
<meta charset="utf-8">
<title>Harrow Grading LLC – Business Card</title>
<link rel="stylesheet" href="https://fonts.googleapis.com/css2?family=Roboto:wght@400;500;700;900&display=swap">
<style>
  :root {
    --stage: #b9b9b9;
    --card-white: #ffffff;
    --card-grey: #666666;
    --brand-orange: #ec6f23;
    --ink: #1e1e1e;
    --ground-grey: #6a6a6a;
  }
  * { box-sizing: border-box; margin: 0; padding: 0; }
  html, body {
    width: 1200px; height: 788px; overflow: hidden;
    background: var(--stage);
    font-family: "Roboto", Arial, sans-serif;
  }
  .stage { position: relative; width: 1200px; height: 788px; }
  .card {
    position: absolute;
    width: 540px; height: 309px;
    border-radius: 22px;
    box-shadow: 0 10px 24px rgba(0,0,0,0.25);
    overflow: hidden;
  }
  .card--front { left: 50px; top: 80px; background: var(--card-white); }
  .card--back { left: 610px; top: 400px; background: var(--card-grey); }

  .brand-name {
    position: absolute; left: 34px; top: 50px;
    width: 270px;
    font-weight: 900; font-size: 22px; letter-spacing: 0.3px;
    color: var(--brand-orange); text-transform: uppercase;
    line-height: 1; white-space: nowrap;
  }
  .accent-bar {
    position: absolute; left: 0; top: 124px;
    width: 10px; height: 48px; background: var(--brand-orange);
  }
  .person { position: absolute; left: 34px; top: 122px; }
  .person__name {
    font-weight: 700; font-size: 21px; color: var(--brand-orange);
    text-transform: uppercase; letter-spacing: 0.5px;
  }
  .person__title { font-size: 16px; color: var(--ink); margin-top: 2px; }

  .contact-list { position: absolute; left: 34px; top: 192px; list-style: none; }
  .contact-list li {
    display: flex; align-items: center; gap: 8px;
    font-size: 14px; color: var(--ink); height: 23px; white-space: nowrap;
  }
  .contact-list svg { width: 12px; height: 12px; flex: none; fill: var(--brand-orange); }

  .machine-art {
    position: absolute; right: 18px; top: 26px;
    width: 196px; height: 262px;
    border-radius: 6px;
    background: linear-gradient(160deg, var(--brand-orange) 0%, #f08a48 60%, var(--ground-grey) 100%);
  }

  .back-name {
    position: absolute; inset: 0;
    display: flex; align-items: center; justify-content: center;
    font-weight: 900; font-size: 34px; letter-spacing: 1px;
    color: #ffffff; text-transform: uppercase;
  }
</style>
</head>
<body>
<main class="stage">
  <section class="card card--front">
    <div class="brand-name">Harrow Grading LLC</div>
    <div class="accent-bar"></div>
    <div class="person">
      <div class="person__name">Dale Mercer</div>
      <div class="person__title">Founder</div>
    </div>
    <ul class="contact-list">
      <li>
        <svg viewBox="0 0 24 24" aria-hidden="true"><path d="M6.6 10.8a15.1 15.1 0 0 0 6.6 6.6l2.2-2.2a1 1 0 0 1 1-.25 11.4 11.4 0 0 0 3.6.57 1 1 0 0 1 1 1V20a1 1 0 0 1-1 1A17 17 0 0 1 3 4a1 1 0 0 1 1-1h3.5a1 1 0 0 1 1 1c0 1.250.2 2.450.57 3.57a1 1 0 0 1-.25 1z"/></svg>
        208-319-4856
      </li>
      <li>
        <svg viewBox="0 0 24 24" aria-hidden="true"><path d="M7 1h10a2 2 0 0 1 2 2v18a2 2 0 0 1-2 2H7a2 2 0 0 1-2-2V3a2 2 0 0 1 2-2zm0 3v14h10V4zm5 15.5a1 1 0 1 0 0 2 1 1 0 0 0 0-2z"/></svg>
        208-417-6290
      </li>
      <li>
        <svg viewBox="0 0 24 24" aria-hidden="true"><path d="M2 5h20v14H2zm2 2v.5l8 5 8-5V7zm0 2.9V17h16V9.9l-8 5z"/></svg>
        harrowgradingllc@maplecove.com
      </li>
      <li>
        <svg viewBox="0 0 24 24" aria-hidden="true"><circle cx="12" cy="12" r="9" fill="none" stroke="#ec6f23" stroke-width="2"/><path d="M3 12h18M12 3c3 3 3 15 0 18M12 3c-3 3-3 15 0 18" fill="none" stroke="#ec6f23" stroke-width="2"/></svg>
        www.harrowgrading.net
      </li>
    </ul>
    <div class="machine-art" role="img" aria-label="Orange illustration of an excavator arm with bucket over a grey ground slope"></div>
  </section>

  <section class="card card--back">
    <div class="back-name">Harrow Grading LLC</div>
  </section>
</main>
</body>
</html>
```